Verdana Crest New Website - Online Learning and Education

New Wordpress website for an online learning site that has courses, worksheets, quizzes, etc.
Updates

We would like something similar to this website: https://hallowaybridgeinstitute.example/mediation-skills-course/. But continue with the content of our current website: http://verdanacrestlearninghub.example

We would like something similar to this site: https://hallowaybridgeinstitute.example/mediation-skills-course/

Coding

Coded - Design and coding required

```html
<!DOCTYPE html>
<html lang="en">
<head>
<meta charset="utf-8">
<title>Verdana Crest – Online Learning</title>
<link href="https://fonts.googleapis.com/css2?family=Lato:wght@400;700;900&display=swap" rel="stylesheet">
<style>
:root{
  --navy:#173a6f;
  --red:#b3121d;
  --text:#4a4a4a;
  --muted:#f3f3f3;
  --line:#dcdcdc;
  --white:#fff;
}
*{margin:0;padding:0;box-sizing:border-box}
html,body{width:1200px;height:3473px;overflow:hidden;background:var(--white)}
body{position:relative;font-family:'Lato',sans-serif;color:var(--text)}
.abs{position:absolute}
.btn{position:absolute;display:flex;align-items:center;justify-content:center;font-weight:700;font-size:13px;letter-spacing:.3px;text-transform:uppercase;color:var(--white);background:var(--red)}
.btn-navy{background:var(--navy)}
.brand{display:flex;align-items:center;gap:10px;font-weight:900;color:var(--navy)}
.brand-dot{border-radius:50%;background:var(--red)}
.nav a{position:absolute;top:96px;font-size:14px;color:#333;text-decoration:none}
.nav a.active{color:var(--red);font-weight:700}
.hero{left:0;top:140px;width:1200px;height:550px;background:linear-gradient(135deg,#8a8378 0%,#6f6558 40%,#4b5a5e 70%,#2f3a38 100%)}
.hero h1{position:absolute;top:195px;width:100%;text-align:center;color:#fff;font-size:50px;font-weight:700;text-shadow:0 2px 6px rgba(0,0,0,.4)}
.hero p{position:absolute;top:262px;left:250px;width:700px;text-align:center;color:#fff;font-size:17px;font-weight:700;line-height:26px;text-shadow:0 1px 4px rgba(0,0,0,.5)}
.dots{position:absolute;top:502px;left:564px;display:flex;gap:8px}
.dots span{width:11px;height:11px;border-radius:50%;background:#fff}
.dots span:first-child{background:var(--red)}
.sec-title{position:absolute;width:1200px;left:0;text-align:center;color:var(--navy);font-weight:900;font-size:27px}
.para{font-size:15px;line-height:25px;color:var(--text)}
.band{left:0;width:1200px;background:var(--muted)}
.card{position:absolute;top:1181px;width:331px}
.card .ph{height:202px;position:relative}
.card .play{position:absolute;left:50%;top:50%;width:32px;height:32px;margin:-16px;border-radius:50%;background:#fff}
.card .play:after{content:"";position:absolute;left:12px;top:9px;border-left:11px solid #333;border-top:7px solid transparent;border-bottom:7px solid transparent}
.card h3{margin-top:20px;font-size:16px;font-weight:900;color:var(--navy)}
.card p{margin-top:8px;font-size:14.5px;line-height:23px}
.card .btn{position:relative;margin-top:17px;width:137px;height:37px}
.h2{font-weight:900;font-size:27px;color:var(--navy)}
.h2-dark{font-weight:900;font-size:24px;color:#2b2b2b}
.post h4,.review h4{font-size:18px;font-weight:700;color:var(--red)}
.review h4{color:var(--navy)}
.post p,.review p{font-size:14.5px;line-height:23px;margin-top:6px}
.meta{font-size:12.5px;color:var(--navy);margin-top:14px}
.stars{color:#f39c12;margin-left:4px;letter-spacing:3px}
.subband{left:0;top:3138px;width:1200px;height:84px;background:var(--red);color:#fff}
.foot h5{font-size:14px;font-weight:700;color:var(--navy);margin-bottom:14px}
.foot li{list-style:none;font-size:13px;color:#444;line-height:32px}
</style>
</head>
<body>

<!-- Header -->
<div class="abs brand" style="left:74px;top:48px;font-size:34px">
  <span class="brand-dot" style="width:40px;height:40px"></span>Verdana Crest
</div>
<svg class="abs" style="left:678px;top:34px" width="18" height="18" viewBox="0 0 24 24"><path fill="#333" d="M6.6 10.8a15.1 15.1 0 0 0 6.6 6.6l2.2-2.2a1 1 0 0 1 1-.25 11.4 11.4 0 0 0 3.6.57 1 1 0 0 1 1 1V20a1 1 0 0 1-1 1A17 17 0 0 1 3 4a1 1 0 0 1 1-1h3.5a1 1 0 0 1 1 1c0 1.25.2 2.45.57 3.6a1 1 0 0 1-.25 1z"/></svg>
<div class="abs" style="left:718px;top:28px;font-size:22px;font-weight:700;color:var(--red)">1-800-555-0142</div>
<div class="btn btn-navy" style="left:909px;top:22px;width:103px;height:39px">Register</div>
<div class="btn" style="left:1022px;top:22px;width:105px;height:39px;background:#fff;color:var(--red);border:1px solid #999">Log In</div>
<nav class="nav">
  <a class="active" style="left:472px">HOME</a>
  <a style="left:553px">ABOUT US</a>
  <a style="left:659px">SERVICES</a>
  <a style="left:762px">COURSES</a>
  <a style="left:863px">BLOG</a>
  <a style="left:937px">REVIEWS</a>
  <a style="left:1035px">CONTACT US</a>
</nav>

<!-- Hero -->
<section class="abs hero" role="img" aria-label="Photo of a young woman studying at a laptop beside a potted plant">
  <h1>Welcome to Verdana Crest</h1>
  <p>Lorem ipsum madolor sit amet, consectetur adipisicing elit, sed do eiusmod tempor coli incididunt ut labore Lorem ipsum madolor sit amet.</p>
  <div class="dots"><span></span><span></span><span></span><span></span></div>
</section>

<!-- Welcome -->
<h2 class="sec-title" style="top:745px">WELCOME TO OUR WEBSITE</h2>
<span class="abs brand-dot" style="left:588px;top:800px;width:24px;height:24px"></span>
<p class="abs para" style="left:74px;top:845px;width:1052px;text-align:center">Lorem ipsum dolor sit amet, consectetur adipiscing elit. Integer vehicula, justo ut convallis auctor, justo eros pulvinar urna, in dignissim leo libero ut lorem. Proin malesuada dapibus enim, eu sollicitudin nunc efficitur vulputate. Donec consequat elit vel neque imperdiet euismod. Suspendisse id viverra dolor, sit amet facilisis nunc. Aenean sed fringilla turpis, ac hendrerit orci.</p>
<div class="btn" style="left:531px;top:949px;width:137px;height:37px">Read More</div>

<!-- Courses -->
<section class="abs band" style="top:1058px;height:667px"></section>
<h2 class="sec-title" style="top:1113px">ONLINE COURSES</h2>
<div class="card" style="left:74px">
  <div class="ph" role="img" aria-label="Photo of a man taking notes with a laptop on a sofa" style="background:linear-gradient(135deg,#b8b3aa,#7d7a74)"><span class="play"></span></div>
  <h3>EXCEPTEUR SINT OCCAECAT</h3>
  <p>Lanventore veritatis et quasi architecto beatae vitae dicta sunt explicabo&nbsp; unde omnis iste natus error sit voluptatem..</p>
  <div class="btn">Watch Video</div>
</div>
<div class="card" style="left:434px">
  <div class="ph" role="img" aria-label="Photo of hands typing on a laptop showing an online courses screen" style="background:linear-gradient(135deg,#d8d6d0,#8f8e88)"><span class="play"></span></div>
  <h3>EXCEPTEUR SINT OCCAECAT</h3>
  <p>Lanventore veritatis et quasi architecto beatae vitae dicta sunt explicabo&nbsp; unde omnis iste natus error sit voluptatem..</p>
  <div class="btn">Watch Video</div>
</div>
<div class="card" style="left:795px">
  <div class="ph" role="img" aria-label="Photo of a smiling woman in an orange blouse writing at a desk" style="background:linear-gradient(135deg,#cfcac0,#d9603a 70%,#b04628)"><span class="play"></span></div>
  <h3>EXCEPTEUR SINT OCCAECAT</h3>
  <p>Lanventore veritatis et quasi architecto beatae vitae dicta sunt explicabo&nbsp; unde omnis iste natus error sit voluptatem..</p>
  <div class="btn">Watch Video</div>
</div>
<div class="btn btn-navy" style="left:464px;top:1614px;width:272px;height:50px;font-size:18px;font-weight:700">View All Courses</div>

<!-- Worksheets -->
<div class="abs" role="img" aria-label="Photo of a student reading a book beside a laptop" style="left:74px;top:1790px;width:512px;height:336px;background:linear-gradient(135deg,#e4e2dc,#a9a59c 60%,#5a3c3c)"></div>
<h2 class="abs h2" style="left:615px;top:1784px">WORKSHEETS</h2>
<div class="abs para" style="left:615px;top:1843px;width:512px">
  <p>Lorem ipsum dolor sit amet, consectetur adipiscing elit. Integer vehicula, justo ut convallis auctor, justo eros pulvinar urna, in dignissim leo libero ut lorem. Proin malesuada dapibus enim, eu sollicitudin nunc efficitur vulputate. Donec consequat elit vel neque imperdiet euismod&nbsp; id viverra dolor,&nbsp; sit amet facilisis nunc enean sed fringilla turpis, ac hendrerit orci.</p>
  <p style="margin-top:11px">Curabitur aliquet felis nec euismod maximus. Nulla at tortor vulputate, pellentesque metus eget, laoreet dolor. Donec porta egestas nunc vitae ullamcorper. Proin dapibus fermentum tempor.</p>
</div>
<div class="btn" style="left:614px;top:2088px;width:137px;height:37px">Read More</div>

<div class="abs" style="left:74px;top:2189px;width:1053px;height:1px;background:var(--line)"></div>

<!-- Quizzes -->
<h2 class="abs h2" style="left:74px;top:2243px">QUIZZES</h2>
<div class="abs para" style="left:74px;top:2303px;width:512px">
  <p>Lorem ipsum dolor sit amet, consectetur adipiscing elit. Integer vehicula, justo ut convallis auctor, justo eros pulvinar urna, in dignissim leo libero ut lorem. Proin malesuada dapibus enim, eu sollicitudin nunc efficitur vulputate. Donec consequat elit vel neque imperdiet euismod&nbsp; id viverra dolor,&nbsp; sit amet facilisis nunc enean sed fringilla turpis, ac hendrerit orci.</p>
  <p style="margin-top:11px">Curabitur aliquet felis nec euismod maximus. Nulla at tortor vulputate, pellentesque metus eget, laoreet dolor. Donec porta egestas nunc vitae ullamcorper. Proin dapibus fermentum tempor.</p>
</div>
<div class="btn" style="left:74px;top:2548px;width:137px;height:37px">Read More</div>
<div class="abs" role="img" aria-label="Photo of a hand marking answers on a tablet quiz sheet" style="left:615px;top:2250px;width:512px;height:334px;background:linear-gradient(135deg,#3a3d36,#e8e8e4 45%,#c9a07a 80%,#6b5a45)"></div>

<!-- Blog & Reviews -->
<section class="abs band" style="top:2673px;height:465px"></section>
<div class="abs" style="left:600px;top:2732px;width:1px;height:350px;background:var(--line)"></div>
<h2 class="abs h2-dark" style="left:73px;top:2724px">BLOG POSTS</h2>
<div class="abs post" style="left:74px;top:2772px;width:494px">
  <h4>EXCEPTEUR SINT OCCAECAT</h4>
  <p>Lanventore veritatis et quasi architecto beatae vitae dicta sunt explicabo unde omnis iste natus error sit voluptatem accusantium laudantium, totam rem aperiam, eaque ipsa..</p>
  <div class="meta">Read More &nbsp;|&nbsp;&nbsp; Posted on 2days ago</div>
</div>
<div class="abs" style="left:74px;top:2927px;width:494px;height:1px;background:var(--line)"></div>
<div class="abs post" style="left:74px;top:2943px;width:494px">
  <h4>EXCEPTEUR SINT OCCAECAT</h4>
  <p>Lanventore veritatis et quasi architecto beatae vitae dicta sunt explicabo unde omnis iste natus error sit voluptatem accusantium laudantium, totam rem aperiam, eaque ipsa..</p>
  <div class="meta">Read More &nbsp;|&nbsp;&nbsp; Posted on 2days ago</div>
</div>

<h2 class="abs h2-dark" style="left:632px;top:2724px">REVIEWS</h2>
<div class="abs" role="img" aria-label="Portrait photo of a reviewer" style="left:632px;top:2780px;width:90px;height:90px;background:linear-gradient(135deg,#d9b24a,#5a3a22)"></div>
<div class="abs review" style="left:740px;top:2780px;width:387px">
  <h4>EXCELLENT<span class="stars">★★★★★</span></h4>
  <p>Lanventore veritatis et quasi architecto beatae vitae dicta sunt explicabo&nbsp; unde omnis iste natus error sit voluptatem accusantium laudantium,</p>
  <div class="meta" style="color:var(--red);margin-top:10px;font-size:13.5px">NAME HEADING</div>
</div>
<div class="abs" style="left:632px;top:2927px;width:495px;height:1px;background:var(--line)"></div>
<div class="abs" role="img" aria-label="Portrait photo of a reviewer" style="left:632px;top:2948px;width:90px;height:90px;background:linear-gradient(135deg,#8a8a86,#3d2e26)"></div>
<div class="abs review" style="left:740px;top:2948px;width:387px">
  <h4>EXCELLENT<span class="stars">★★★★★</span></h4>
  <p>Lanventore veritatis et quasi architecto beatae vitae dicta sunt explicabo&nbsp; unde omnis iste natus error sit voluptatem accusantium laudantium,</p>
  <div class="meta" style="color:var(--red);margin-top:10px;font-size:13.5px">NAME HEADING</div>
</div>

<!-- Subscribe -->
<section class="abs subband">
  <div class="abs" style="left:75px;top:30px;font-size:18px;font-weight:700">SUBSCRIBE EMAIL</div>
  <div class="abs" style="left:255px;top:23px;width:256px;height:38px;background:#fff;color:#333;font-size:11px;font-weight:700;padding:13px 10px">Enter Email Address</div>
  <div class="abs" style="left:518px;top:23px;width:102px;height:38px;background:#222;color:#fff;font-size:11px;font-weight:700;display:flex;align-items:center;justify-content:center">SUBSCRIBE</div>
  <div class="abs" style="left:794px;top:30px;font-size:18px;font-weight:700">FOLLOW US</div>
  <div class="abs" style="left:918px;top:30px;display:flex;gap:22px">
    <span style="width:24px;height:24px;border-radius:50%;background:#fff"></span>
    <span style="width:24px;height:24px;border-radius:50%;background:#fff"></span>
    <span style="width:24px;height:24px;border-radius:50%;background:#fff"></span>
    <span style="width:24px;height:24px;border-radius:50%;background:#fff"></span>
    <span style="width:24px;height:24px;border-radius:50%;background:#fff"></span>
  </div>
</section>

<!-- Footer -->
<footer class="foot">
  <div class="abs brand" style="left:75px;top:3300px;font-size:24px">
    <span class="brand-dot" style="width:30px;height:30px"></span>Verdana Crest
  </div>
  <div class="abs" style="left:75px;top:3360px;font-size:12.5px;line-height:22px;color:#444">Copyright © 2019, Company Name<br>All Right reserved</div>
  <div class="abs" style="left:356px;top:3274px">
    <h5>QUICK LINKS</h5>
    <ul style="display:grid;grid-template-columns:100px 100px"><li>Home</li><li>Blog</li><li>About Us</li><li>Reviews</li><li>Services</li><li>Contact Us</li><li>Courses</li></ul>
  </div>
  <div class="abs" style="left:636px;top:3274px">
    <h5>RESOURCES</h5>
    <ul><li>Cepteur sint</li><li>Lccaecat cupidatat</li><li>Non proident, sunt</li><li>Culpa qui officia deserunt</li></ul>
  </div>
  <div class="abs" style="left:885px;top:3274px;width:240px">
    <h5>CONTACT INFO</h5>
    <div style="display:grid;grid-template-columns:33px 1fr;font-size:13px;line-height:20px;color:#444;row-gap:10px;margin-top:6px">
      <svg width="12" height="14" viewBox="0 0 24 24"><path fill="#333" d="M12 2a7 7 0 0 0-7 7c0 5 7 13 7 13s7-8 7-13a7 7 0 0 0-7-7zm0 9.5A2.5 2.5 0 1 1 12 6.5a2.5 2.5 0 0 1 0 5z"/></svg>
      <div>14 Harbor Lane, Street Name<br>Springfield, USA</div>
      <svg width="12" height="12" viewBox="0 0 24 24"><path fill="#333" d="M6.6 10.8a15.1 15.1 0 0 0 6.6 6.6l2.2-2.2a1 1 0 0 1 1-.25 11.4 11.4 0 0 0 3.6.57 1 1 0 0 1 1 1V20a1 1 0 0 1-1 1A17 17 0 0 1 3 4a1 1 0 0 1 1-1h3.5a1 1 0 0 1 1 1c0 1.25.2 2.45.57 3.6a1 1 0 0 1-.25 1z"/></svg>
      <div>1-800-555-0142</div>
      <svg width="13" height="12" viewBox="0 0 24 20"><path fill="#333" d="M2 2h20v16H2zm2 2v1l8 5 8-5V4z"/></svg>
      <div>hello@verdanacrest.example</div>
    </div>
  </div>
</footer>
</body>
</html>
```